KRL Stationery Design Project

Dear Designers,
We need a new stationery design for company to match our new logo.
Designers should provide a design for the following:
1. Business Card: 3.5x2 Inches.
2. Letterhead: A4 size.
3. Envelops: 25x35.5 Cm.
You can keep the Arabic name at the bottom of the logo Or you can use the separate attached Arabic Name.
Please refer to the attached logo guide for design information.
Sample Business Card information:
Name: Tarek Sowan
Position: Operation Manager
Tel: +966 920007164 Ex. 500
Fax: +966 (3)8842617
Mob: +966 (5)00263817
email: tarek@krl-example.com.sa
URL: www.krl-example.com.sa
Address:
Nakheel Heights, Suite 718
Zayed bin Omar Str.
Khobar, 31847
Saudi Arabia
Updates
Dear All,
Please note, we had uploaded our logo along with Arabic writing in Adobe illustrator format (.ai).
Regards,
Karim
Dear All,
A sample data for the business card had been added as per your request.
Regards,
Karim

```html
<!DOCTYPE html>
<html lang="en">
<head>
<meta charset="utf-8">
<title>KRL Business Card</title>
<link rel="stylesheet" href="https://fonts.googleapis.com/css2?family=Open+Sans:wght@400;600;700;800&display=swap">
<style>
  :root {
    --stage: #2f2f31;
    --paper: #ffffff;
    --navy: #0d2a4f;
    --silver: #9a9b9e;
    --silver-light: #b9babd;
    --ink: #2b2b2b;
    --back-grey: #9c9d9f;
  }
  * { margin: 0; padding: 0; box-sizing: border-box; }
  html, body { width: 1200px; height: 472px; overflow: hidden; }
  body {
    background: var(--stage);
    font-family: "Open Sans", Arial, sans-serif;
    position: relative;
  }
  .card {
    position: absolute;
    top: 85px;
    width: 523px;
    height: 298px;
    overflow: hidden;
  }
  .card--front { left: 50px; background: var(--paper); }
  .card--back { left: 613px; background: var(--back-grey); }

  .card__waves { position: absolute; inset: 0; width: 100%; height: 100%; }

  .brand {
    position: absolute;
    display: flex;
    align-items: center;
    gap: 12px;
    font-weight: 800;
    font-size: 58px;
    letter-spacing: 2px;
    line-height: 1;
  }
  .brand__dot { width: 18px; height: 18px; border-radius: 50%; }
  .card--front .brand { left: 178px; top: 40px; color: var(--navy); }
  .card--front .brand__dot { background: var(--silver); }
  .card--back .brand { left: 178px; top: 98px; color: #ffffff; }
  .card--back .brand__dot { background: #ffffff; }

  .contact {
    position: absolute;
    left: 124px;
    top: 160px;
    color: var(--ink);
    font-size: 13.5px;
    line-height: 18px;
  }
  .contact__grid {
    display: grid;
    grid-template-columns: 130px auto;
    margin-left: 0;
    padding-left: 0;
  }
  .contact__item { display: flex; align-items: center; gap: 6px; }
  .contact__item svg { width: 11px; height: 11px; fill: var(--ink); flex: none; }
  .contact__address { margin-left: -36px; margin-top: 2px; white-space: nowrap; }

  .holder-name {
    position: absolute;
    left: 321px;
    top: 259px;
    color: #ffffff;
    font-weight: 700;
    font-size: 15px;
    letter-spacing: 0.2px;
  }
  .card--back .web {
    position: absolute;
    left: 0;
    width: 100%;
    top: 205px;
    text-align: center;
    color: var(--navy);
    font-size: 12.5px;
    font-weight: 600;
    letter-spacing: 2px;
  }
</style>
</head>
<body>
  <section class="card card--front" aria-label="Business card front">
    <svg class="card__waves" viewBox="0 0 523 298" preserveAspectRatio="none" aria-hidden="true">
      <path fill="var(--navy)" d="M0 145 C 20 205, 90 250, 210 262 C 330 272, 430 250, 523 238 L523 298 L0 298 Z"/>
      <path fill="var(--paper)" d="M0 175 C 40 220, 130 244, 230 246 C 330 248, 430 232, 523 222 L523 236 C 430 246, 330 264, 220 258 C 120 252, 40 225, 0 190 Z"/>
      <path fill="var(--silver-light)" d="M40 210 C 120 240, 230 240, 330 225 C 420 212, 480 210, 523 212 L523 230 C 460 230, 380 244, 280 252 C 180 258, 100 240, 40 210 Z"/>
    </svg>

    <div class="brand"><span class="brand__name">KRL</span><span class="brand__dot"></span></div>

    <div class="contact">
      <div class="contact__grid">
        <div class="contact__item">
          <svg viewBox="0 0 12 12"><path d="M2.5 1 L4.5 1 L5.3 3.6 L4 4.6 C4.6 6 5.8 7.3 7.4 8 L8.4 6.7 L11 7.5 L11 9.5 C11 10.4 10.3 11 9.4 11 C4.8 10.6 1.4 7.2 1 2.6 C1 1.7 1.6 1 2.5 1 Z"/></svg>
          <span>123-456-7890</span>
        </div>
        <div class="contact__item">
          <svg viewBox="0 0 12 12"><path d="M1 3 L11 3 L11 10 L1 10 Z M1.8 3.6 L6 7 L10.2 3.6 L10.2 4.6 L6 8 L1.8 4.6 Z" fill-rule="evenodd"/></svg>
          <span>info@krl-example.com.sa</span>
        </div>
        <div class="contact__item">
          <svg viewBox="0 0 12 12"><path d="M3 1 L8 1 L8 4 L10.5 4 C11 4 11.3 4.4 11.3 4.8 L11.3 9 L0.7 9 L0.7 4.8 C0.7 4.4 1 4 1.5 4 L3 4 Z M2 10 L10 10 L10 11 L2 11 Z"/></svg>
          <span>123-456-7890</span>
        </div>
        <div class="contact__item">
          <svg viewBox="0 0 12 12"><circle cx="6" cy="6" r="5"/></svg>
          <span>www.krl-example.com.sa</span>
        </div>
      </div>
      <p class="contact__address">Street Name, City Name State, City Zip 123 4560</p>
    </div>

    <p class="holder-name">YOUR NAME</p>
  </section>

  <section class="card card--back" aria-label="Business card back">
    <div class="brand"><span class="brand__name">KRL</span><span class="brand__dot"></span></div>
    <p class="web">www.krl-example.com.sa</p>
  </section>
</body>
</html>
```